HOT TUB - SPAS service needs an business card

I need an business for my company who his specialise in a maintenance,water treatment and cleaning of Hot Tub - Spas for commercial and residential customers. The company operate mainly in the ski resort of Chamonix, Megève and St Gervais. The final product should communicate pure water, cleanest and professional for luxury property's.
I have upload a logo but any improvement on it is welcome.(color,size, details etc..) or any other idea. Thank you
Company Name: 58 BAINS
My name: Lucien Marchetti
Email: lucimarch@examplemail.net
Tel: +33 (0)6 71 58 29 64
Description to be on the card in french(first langage) and in English:
- Spas service
- Entretien, traitement eau, nettoyage.
- Maintenance, water treatment, cleaning.
Industry/Entity Type
Residential
Colors
Designer to choose colors to be used in the design.
Look and feel
Each slider illustrates characteristics of the customer's brand and the style your logo design should communicate.

```html
<!DOCTYPE html>
<html lang="fr">
<head>
<meta charset="utf-8">
<title>58 BAINS – Business card</title>
<link rel="stylesheet" href="https://fonts.googleapis.com/css2?family=PT+Sans:wght@400;700&display=swap">
<style>
  :root {
    --page: #ebe8e3;
    --front-blue: #1ea3fb;
    --back-blue: #0e78dd;
    --band-dark: #0f5fd0;
    --band-light: #a8d8fb;
    --white: #ffffff;
    --font: "PT Sans", "Helvetica Neue", Arial, sans-serif;
  }
  * { box-sizing: border-box; margin: 0; padding: 0; }
  html, body {
    width: 1200px; height: 1099px; overflow: hidden;
    background: var(--page);
    font-family: var(--font);
    color: var(--white);
  }
  .card {
    position: absolute;
    width: 862px; height: 492px;
    overflow: hidden;
    box-shadow: 0 3px 10px rgba(0,0,0,0.18);
  }
  .card-front { left: 50px; top: 57px; background: var(--front-blue); }
  .card-back  { left: 267px; top: 579px; background: var(--back-blue); }

  .brand-name {
    position: absolute;
    font-weight: 700;
    letter-spacing: 1px;
    line-height: 1;
    white-space: nowrap;
  }
  .card-front .brand-name { left: 151px; top: 160px; font-size: 64px; }
  .card-back .brand-name { left: 0; right: 0; top: 150px; text-align: center; font-size: 64px; }

  .holder-name {
    position: absolute; left: 83px; top: 350px;
    font-size: 29px; font-weight: 700; line-height: 1;
  }
  .divider {
    position: absolute; left: 380px; top: 327px;
    width: 1px; height: 80px; background: var(--white);
  }
  .contact {
    position: absolute; left: 405px;
    display: flex; align-items: center; gap: 12px;
    font-size: 28px; line-height: 1; white-space: nowrap;
  }
  .contact-phone { top: 331px; font-weight: 700; }
  .contact-email { top: 377px; }
  .contact svg { width: 26px; height: 26px; flex: none; }

  .footer-band { position: absolute; left: 0; bottom: 0; width: 862px; height: 23px; }

  .services-title {
    position: absolute; left: 0; right: 0; top: 343px;
    text-align: center; font-size: 31px; font-weight: 700; line-height: 1;
  }
  .services-line {
    position: absolute; left: 0; right: 0;
    text-align: center; font-size: 30px; line-height: 1; word-spacing: 1px;
  }
  .services-fr { top: 395px; }
  .services-en { top: 434px; }
</style>
</head>
<body>

<section class="card card-front">
  <div class="brand-name">58 BAINS</div>
  <div class="holder-name">Lucien Marchetti</div>
  <div class="divider"></div>
  <div class="contact contact-phone">
    <svg viewBox="0 0 24 24" aria-hidden="true"><circle cx="12" cy="12" r="10.5" fill="none" stroke="#fff" stroke-width="1.6"/><path d="M8.5 6.5c-1 1 -1 3 .8 6s3.8 4.8 5.5 5c.9.1 1.6-.6 1.8-1.3l-2.3-1.6-1.1 .9c-1-.5-2.6-2.4-3.1-3.6l1-1-1.2-2.6z" fill="#fff"/></svg>
    <span>+33 (0)6 71 58 29 64</span>
  </div>
  <div class="contact contact-email">
    <svg viewBox="0 0 24 24" aria-hidden="true"><path d="M2 10l10-6 10 6v10H2z" fill="#fff"/><path d="M2 10l10 6 10-6" fill="none" stroke="#1ea3fb" stroke-width="1.6"/><path d="M8 9h8M8 11.5h8" stroke="#1ea3fb" stroke-width="1.2"/></svg>
    <span>lucimarch@examplemail.net</span>
  </div>
  <svg class="footer-band" viewBox="0 0 862 23" preserveAspectRatio="none" aria-hidden="true">
    <polygon points="0,0 400,0 375,23 0,23" fill="var(--band-dark)"/>
    <polygon points="400,0 862,0 862,23 375,23" fill="var(--band-light)"/>
    <polygon points="400,0 415,0 390,23 375,23" fill="#c9e7fd"/>
  </svg>
</section>

<section class="card card-back">
  <div class="brand-name">58 BAINS</div>
  <div class="services-title">SPAS SERVICES</div>
  <div class="services-line services-fr">•Entretien&nbsp; •traitement eau&nbsp; •nettoyage</div>
  <div class="services-line services-en">•Maintenance&nbsp; •water treatment&nbsp; •cleaning.</div>
</section>

</body>
</html>
```